Tamsin Vale Chiropractic Web Design

We need a fully operating Web site design INCLUDING the code for a Chiropractic Clinic based in Auckland New Zealand to target people from different financial backgrounds.

We need 4 Pages as followed:
1. Home: includes Slideshow of the clinic, General information about chiropractic, option for "Request an appointment", and it would be nice to have a picture on the top right side of the header and the clinic's name and logo on the top left side. on the bottom right we would like a small section for "Testimonial" (A good example: http://www.brightfernimaging.com/ )
(A good example for slide show is: http://www.drpolk.co.nz/)
(A good example for the header is: http://www.spinalworksbrx.com/)

2. About Us: this section will include the background information of the company, and a section for our staff (which will includes a photo and description of each person/staff which can be changedanytime)
(a good example: http://www.maplerowchiro.co.nz/)

3. Contact: includes location, map, contact numbers, email, and a contact box (A good example: http://www.brightfernimaging.com/contact/)

4. Services: includes our products, adjustment equipment, chiropractic products for sale, few pictures of patients while under chiropractic care/adjustment tables

We would also like to add "social networking" options on the bottom left side of every page (Facebook, twitter, Blog, Google+)

Please check the following links to get a feel of our favorite designs:
http://www.spinalworksbrx.com/
http://www.maplerowchiro.co.nz/
http://www.drpolk.co.nz/
http://www.fenwickchiropracticclinic.com/
http://www.quietbloom.co.nz/
http://www.pwt.net.nz/index-1.html
http://home.corebalancechiro.co.nz/home/

we would like to have full access to the back-end- admin of the website to be able to change and add any pictures or texts.
Updates

Hi Lovely Designer,

thank you so much for your proposed designs. We just uploaded the original source file of our logo, for you all to have access on it to facilitate your work. 

Enjoy your day

Lena

Target Market(s)

People with different financial background as well as we are located in the artistic part of town, so appealing to those crowd is important to us.

Industry/Entity Type

Financial

Requirements
Must have
• 1.color similar to the logo or darker colors (Dark and rich colors are prefered)
2. more artistic than a basic doctors' clinic
3. I would like the opening of the web to bring art, tranquility and peaceful images into mind
Should not have
• Not bombarded with lots of info and pics in one page, not too busy and crowded

```html
<!DOCTYPE html>
<html lang="en">
<head>
<meta charset="utf-8">
<title>Tamsin Vale Chiropractic</title>
<link rel="stylesheet" href="https://fonts.googleapis.com/css2?family=Source+Sans+3:wght@400;600&family=Arimo:ital,wght@0,400;0,700;1,400&display=swap">
<style>
:root{
  --navy:#0b2a5a;
  --navy-box:#0c2b5c;
  --lime:#9cba35;
  --olive:#7b9a2a;
  --sage-top:#a8c6b0;
  --sage-bot:#7fa08a;
  --paper:#ececec;
  --ink:#1c1c1c;
  --footer:#333333;
  --white:#ffffff;
  --star:#f2994a;
}
*{box-sizing:border-box;margin:0;padding:0}
html,body{width:1088px;height:1200px;overflow:hidden}
body{position:relative;background:var(--paper);font-family:"Arimo",Arial,sans-serif;color:var(--ink)}
.abs{position:absolute}

.site-header{left:0;top:0;width:1088px;height:112px;background:var(--navy)}
.header-rule{left:0;top:112px;width:1088px;height:6px;background:#a9c3b3}
.brand{left:112px;top:30px;color:var(--white);font-family:"Source Sans 3",sans-serif;font-weight:400;font-size:25px;line-height:27px;letter-spacing:.5px}
.brand-dot{left:112px;top:38px;width:0;height:0}
.call-label{right:114px;top:38px;color:var(--white);font-family:"Source Sans 3",sans-serif;font-size:19px}
.call-number{right:108px;top:66px;color:var(--lime);font-family:"Source Sans 3",sans-serif;font-size:21px}
.call-icon{left:832px;top:68px}

.main-nav{left:0;top:118px;width:1088px;height:43px;background:linear-gradient(#fbfbfb,#dcdcdc);display:flex}
.main-nav a{position:absolute;top:0;height:43px;line-height:43px;font-size:15px;color:#2a2a2a;text-decoration:none;transform:translateX(-50%)}
.nav-divider{position:absolute;top:0;width:1px;height:43px;background:#c4c4c4;box-shadow:1px 0 0 #fff}

.hero{left:0;top:161px;width:1088px;height:371px;background:linear-gradient(var(--sage-top),var(--sage-bot))}
.slider-frame{left:109px;top:180px;width:870px;height:332px;background:var(--white);box-shadow:0 10px 12px -6px rgba(0,0,0,.35)}
.slide-photo{left:115px;top:184px;width:860px;height:325px;background:linear-gradient(100deg,#8fa9b9 0%,#c9d4d8 40%,#e8e3d8 60%,#b7c8cf 100%)}
.slider-arrow{top:311px;width:30px;height:34px;background:#000}
.slider-arrow svg{display:block;margin:9px auto}
.slide-caption{left:733px;top:405px;width:242px;height:104px;background:rgba(255,255,255,.82);text-align:center;font-family:"Source Sans 3",sans-serif;font-size:27px;line-height:32px;padding-top:4px;color:var(--navy)}
.slide-caption .accent{color:var(--lime)}

.section-title{font-family:"Source Sans 3",sans-serif;font-size:17px;color:var(--navy);letter-spacing:-.2px}
.section-title span{color:var(--olive)}
.dotted{height:0;border-top:1px dotted #a8a8a8}
.body-copy{font-size:11.2px;line-height:16.3px;text-align:justify}

.service-photo{left:119px;top:893px;width:207px;height:141px;background:linear-gradient(135deg,#c59a82,#e9ddd6 55%,#d7c7bd);border:3px solid #9a9a9a}
.service-item{left:340px;width:376px;font-size:11.2px;line-height:16.3px}
.service-item svg{position:absolute;left:0;top:4px}
.service-item p{margin-left:18px}

.appointment{left:765px;top:582px;width:217px;height:239px;border:2px solid var(--navy);background:var(--navy)}
.appointment-photo{left:0;top:0;width:213px;height:164px;background:linear-gradient(120deg,#cfe3f2,#6fa9d6 60%,#e6eef5)}
.appointment-band{left:0;top:164px;width:213px;height:71px;background:#0e4478}
.appointment-label{left:24px;top:177px;color:var(--white);font-family:"Source Sans 3",sans-serif;font-weight:600;font-size:20px;line-height:22px}
.appointment-icon{left:142px;top:170px}

.testimonials{left:764px;top:838px;width:217px;height:238px;background:var(--navy-box);color:var(--white)}
.testimonials h2{position:absolute;left:29px;top:13px;font-family:"Source Sans 3",sans-serif;font-weight:400;font-size:17px}
.testimonials .rule{position:absolute;left:14px;top:44px;width:187px;border-top:1px dashed #8aa0c2}
.quote{position:absolute;left:10px;width:200px;text-align:center;font-size:10.4px;line-height:16px}
.stars{position:absolute;left:122px}
.byline{position:absolute;right:17px;font-size:10.4px;font-style:italic}

.site-footer{left:0;top:1088px;width:1088px;height:112px;background:var(--footer);color:var(--white)}
.stay{left:118px;top:1102px;font-family:"Source Sans 3",sans-serif;font-size:17px;color:var(--white)}
.social{top:1136px;width:35px;height:35px;border-radius:50%;background:var(--white)}
.footer-nav{top:1119px;font-size:12.8px;color:var(--white)}
.copyright{right:114px;top:1162px;font-size:11.6px;color:var(--white)}
</style>
</head>
<body>

<header class="abs site-header"></header>
<div class="abs header-rule"></div>
<div class="abs brand">Tamsin Vale<br>Chiropractic</div>
<div class="abs call-label">Call Now</div>
<svg class="abs call-icon" width="24" height="24" viewBox="0 0 24 24" aria-hidden="true">
  <circle cx="12" cy="12" r="12" fill="#e9ecef"/>
  <path d="M8.2 6.5l2 2.3-1.1 1.6c.8 1.8 2 3 3.8 3.8l1.6-1.1 2.3 2-1.1 2c-4.6-.2-8.6-4.2-8.8-8.8z" fill="#555"/>
</svg>
<div class="abs call-number">604-555-0187</div>

<nav class="abs main-nav">
  <a href="#" style="left:168px">Home</a>
  <span class="nav-divider" style="left:267px"></span>
  <a href="#" style="left:361px">Aboout Us</a>
  <span class="nav-divider" style="left:456px"></span>
  <a href="#" style="left:548px">Services</a>
  <span class="nav-divider" style="left:646px"></span>
  <a href="#" style="left:736px">Testimonials</a>
  <span class="nav-divider" style="left:834px"></span>
  <a href="#" style="left:909px">Contact Us</a>
</nav>

<section class="abs hero"></section>
<div class="abs slider-frame"></div>
<div class="abs slide-photo" role="img" aria-label="Slideshow photo of a smiling family sitting outside a house"></div>
<div class="abs slider-arrow" style="left:110px"><svg width="10" height="16" viewBox="0 0 10 16"><path d="M8 1L2 8l6 7" stroke="#fff" stroke-width="2.5" fill="none"/></svg></div>
<div class="abs slider-arrow" style="left:948px"><svg width="10" height="16" viewBox="0 0 10 16"><path d="M2 1l6 7-6 7" stroke="#fff" stroke-width="2.5" fill="none"/></svg></div>
<div class="abs slide-caption"><span class="accent">Restoring Health</span><br>To<br>Your Body</div>

<h1 class="abs section-title" style="left:118px;top:564px">WELCOME TO <span>TAMSIN VALE CHIROPRACTIC</span></h1>
<div class="abs dotted" style="left:118px;top:597px;width:594px"></div>

<p class="abs body-copy" style="left:118px;top:618px;width:604px"><b>Lorem Ipsum is simply dummy text of the printing and typesetting industry. Lorem Ipsum has been the industry's standard</b> dummy text ever since the 1500s, when an unknown printer took a galley of type and scrambled it to make a type specimen book. It has survived not only five centuries, but also the leap into electronic typesetting, remaining essentially unch Lorem Ipsum is simply dummy text of the printing and typesetting industry.</p>
<p class="abs body-copy" style="left:118px;top:699px;width:598px">Lorem Ipsum is simply dummy text of the printing and typesetting industry. Lorem Ipsum has been the industry's stananged.Lorem Ipsum is simply dummy text of the printing and typesetting industry.</p>
<p class="abs body-copy" style="left:118px;top:748px;width:598px">&nbsp;Lorem Ipsum has been the industry's Lorem Ipsum is simply dummy text of the printing and typesetting industry. Lorem Ipsum has been the industry's stananged.Lorem Ipsum is simply dummy text of the printing and typesetting industry. Lorem Ipsum has been the industry's</p>

<h2 class="abs section-title" style="left:120px;top:822px">OUR <span>SERVICES</span></h2>
<div class="abs dotted" style="left:120px;top:856px;width:594px"></div>

<div class="abs service-photo" role="img" aria-label="Photo of hands giving a back adjustment"></div>
<div class="abs service-item" style="top:893px"><svg width="9" height="7" viewBox="0 0 9 7"><path d="M0 0l3 3.5L0 7M5 0l3 3.5L5 7" stroke="#0b2a5a" stroke-width="1.5" fill="none"/></svg><p>Lorem Ipsum has been the industry's Lorem Ipsum is simply dummy text of the printing and typesetting industry.</p></div>
<div class="abs service-item" style="top:951px"><svg width="9" height="7" viewBox="0 0 9 7"><path d="M0 0l3 3.5L0 7M5 0l3 3.5L5 7" stroke="#0b2a5a" stroke-width="1.5" fill="none"/></svg><p>Lorem Ipsum has been the industry's Lorem Ipsum is simply dummy text of the printing and typesetting industry.</p></div>
<div class="abs service-item" style="top:1004px"><svg width="9" height="7" viewBox="0 0 9 7"><path d="M0 0l3 3.5L0 7M5 0l3 3.5L5 7" stroke="#0b2a5a" stroke-width="1.5" fill="none"/></svg><p>Lorem Ipsum has been the industry's Lorem Ipsum is simply dummy text of the printing and typesetting industry.</p></div>

<aside class="abs appointment">
  <div class="abs appointment-photo" role="img" aria-label="Photo of a chiropractor in a white coat beside a spine model"></div>
  <div class="abs appointment-band"></div>
  <div class="abs appointment-label">Make An<br>Appointment</div>
  <svg class="abs appointment-icon" width="58" height="62" viewBox="0 0 58 62" aria-hidden="true">
    <rect x="8" y="8" width="40" height="48" rx="4" fill="none" stroke="#fff" stroke-width="3" transform="rotate(-12 28 32)"/>
    <rect x="20" y="4" width="16" height="8" rx="2" fill="#fff" transform="rotate(-12 28 32)"/>
    <path d="M18 30h20M18 38h20M18 46h14" stroke="#fff" stroke-width="2.5" transform="rotate(-12 28 32)"/>
  </svg>
</aside>

<aside class="abs testimonials">
  <h2>CLINTS TESTIMONIALS</h2>
  <div class="rule"></div>
  <p class="quote" style="top:64px">Lorem Ipsum is simply dummy text of the printing and typesetting industry.</p>
  <svg class="stars" style="top:99px" width="78" height="15" viewBox="0 0 78 15" aria-label="Five stars">
    <defs><path id="star" d="M7.5 0l2.2 4.7 5.1.6-3.8 3.5 1 5.1-4.5-2.6-4.5 2.6 1-5.1L.2 5.3l5.1-.6z"/></defs>
    <use href="#star" x="0" fill="var(--star)"/><use href="#star" x="15.5" fill="var(--star)"/><use href="#star" x="31" fill="var(--star)"/><use href="#star" x="46.5" fill="var(--star)"/><use href="#star" x="62" fill="var(--star)"/>
  </svg>
  <p class="byline" style="top:127px">May 12, 2013 by Marisol</p>
  <p class="quote" style="top:148px;left:13px">Lorem Ipsum is simply dummy text of the printing and typesetting industry.</p>
  <svg class="stars" style="top:184px;left:124px" width="78" height="15" viewBox="0 0 78 15" aria-label="Five stars">
    <use href="#star" x="0" fill="var(--star)"/><use href="#star" x="15.5" fill="var(--star)"/><use href="#star" x="31" fill="var(--star)"/><use href="#star" x="46.5" fill="var(--star)"/><use href="#star" x="62" fill="var(--star)"/>
  </svg>
  <p class="byline" style="top:212px">May 12, 2013 by Marisol</p>
</aside>

<footer class="abs site-footer"></footer>
<div class="abs stay">Stay Connected</div>
<span class="abs social" style="left:117px" aria-label="Social link"></span>
<span class="abs social" style="left:164px" aria-label="Social link"></span>
<span class="abs social" style="left:213px" aria-label="Social link"></span>
<span class="abs social" style="left:260px" aria-label="Social link"></span>

<span class="abs footer-nav" style="left:491px">Home</span>
<span class="abs footer-nav" style="left:548px">-</span>
<span class="abs footer-nav" style="left:581px">Aboout Us</span>
<span class="abs footer-nav" style="left:675px">-</span>
<span class="abs footer-nav" style="left:705px">Services</span>
<span class="abs footer-nav" style="left:778px">-</span>
<span class="abs footer-nav" style="left:800px">Testimonials</span>
<span class="abs footer-nav" style="left:887px">-</span>
<span class="abs footer-nav" style="left:909px">Contact Us</span>
<div class="abs copyright">Copyright (C)Tamsin Vale Chiropractic 2013 - 2014 .&nbsp; All Rights Reserved</div>

</body>
</html>
```